A clean crisp business card for a Landscape Construction company. Designed to be easy to read contact/ info and also be appealing/interesting, unlike a traditional business card.

Industry/Entity Type

Landscape Construction

Contact Information for Business Card

Company name : Brambleford Landscape Construction, phone number: (877) 62Vista, website:Bramblefordyards.example, Email, sales@bramblefordyards.example

Requirements
Nice to have
• Luxurious finishes/ details…. Icons or emblems next to contact info
Should not have
• Clipart or general pictures

```html
<!DOCTYPE html>
<html lang="en">
<head>
<meta charset="utf-8">
<title>Brambleford Landscape Construction – Business Card</title>
<link href="https://fonts.googleapis.com/css2?family=Cinzel:wght@500&family=Arimo:wght@400&display=swap" rel="stylesheet">
<style>
  :root {
    --bg: #3a302c;
    --card: #171717;
    --card-edge: #8cc63f;
    --brand-blue: #1f6fd1;
    --leaf-green: #a6d23a;
    --text-light: #f2f2f2;
  }
  * { box-sizing: border-box; margin: 0; padding: 0; }
  html, body { width: 1200px; height: 716px; overflow: hidden; }
  body {
    background: var(--bg);
    position: relative;
    font-family: "Arimo", Arial, sans-serif;
  }
  .card {
    position: absolute;
    width: 520px;
    height: 300px;
    top: 208px;
    background: var(--card);
    border-bottom: 2px solid var(--card-edge);
    border-left: 1px solid var(--card-edge);
    box-shadow: 0 14px 30px rgba(0,0,0,.45);
    overflow: hidden;
  }
  .card--front { left: 50px; }
  .card--back { left: 630px; }

  .wordmark {
    font-family: "Cinzel", "Times New Roman", serif;
    font-weight: 500;
    color: var(--brand-blue);
    text-align: center;
    line-height: 1.15;
    letter-spacing: .04em;
  }
  .card--front .wordmark {
    position: absolute;
    left: 0; right: 0; top: 112px;
    font-size: 30px;
  }
  .card--front .wordmark .wordmark__sub { font-size: 16px; letter-spacing: .22em; display: block; margin-top: 6px; }

  .wave { position: absolute; inset: 0; width: 100%; height: 100%; }

  .card--back .wordmark {
    position: absolute;
    left: 24px; top: 96px;
    width: 250px;
    font-size: 22px;
    text-align: left;
  }
  .card--back .wordmark .wordmark__sub { font-size: 11.5px; letter-spacing: .2em; display: block; margin-top: 4px; }

  .rule {
    position: absolute;
    height: 1px;
    background: var(--leaf-green);
  }
  .rule--logo { left: 24px; top: 166px; width: 300px; }
  .rule--name { right: 24px; top: 270px; width: 240px; }

  .contact-list {
    position: absolute;
    left: 24px; top: 182px;
    list-style: none;
    color: var(--text-light);
    font-size: 13px;
  }
  .contact-list li { display: flex; align-items: center; gap: 8px; height: 22px; }
  .contact-list svg { width: 12px; height: 12px; flex: none; }

  .person {
    position: absolute;
    right: 28px; top: 200px;
    text-align: right;
    font-family: "Cinzel", "Times New Roman", serif;
    font-weight: 500;
  }
  .person__name { color: var(--brand-blue); font-size: 24px; letter-spacing: .04em; }
  .person__role { color: var(--leaf-green); font-size: 15px; letter-spacing: .08em; margin-top: 2px; }
</style>
</head>
<body>

<section class="card card--front">
  <p class="wordmark">Brambleford<span class="wordmark__sub">Landscape Construction</span></p>
</section>

<section class="card card--back">
  <svg class="wave" viewBox="0 0 520 300" preserveAspectRatio="none" aria-hidden="true">
    <path d="M0,58 C100,30 200,22 270,52 C340,82 420,126 520,130 V0 H0 Z" fill="var(--leaf-green)"/>
    <path d="M0,48 C100,20 200,12 270,42 C340,72 420,116 520,120 V0 H0 Z" fill="var(--card)"/>
    <path d="M0,42 C100,14 200,6 270,36 C340,66 420,110 520,114 V0 H0 Z" fill="var(--brand-blue)"/>
  </svg>

  <p class="wordmark">Brambleford<span class="wordmark__sub">Landscape Construction</span></p>
  <div class="rule rule--logo"></div>

  <ul class="contact-list">
    <li>
      <svg viewBox="0 0 12 12"><path d="M3 1 L5 3.5 L4 5 C4.6 6.4 5.6 7.4 7 8 L8.5 7 L11 9 L9.8 11 C5.5 10.8 1.2 6.5 1 2.2 Z" fill="var(--leaf-green)"/></svg>
      (877) 62Vista
    </li>
    <li>
      <svg viewBox="0 0 12 12"><rect x="1" y="2.5" width="10" height="7" fill="none" stroke="var(--leaf-green)" stroke-width="1.2"/><path d="M1 2.5 L6 6.5 L11 2.5" fill="none" stroke="var(--leaf-green)" stroke-width="1.2"/></svg>
      sales@bramblefordyards.example
    </li>
    <li>
      <svg viewBox="0 0 12 12"><circle cx="6" cy="6" r="5" fill="none" stroke="var(--leaf-green)" stroke-width="1.1"/><ellipse cx="6" cy="6" rx="2.2" ry="5" fill="none" stroke="var(--leaf-green)" stroke-width="1"/><path d="M1 6 H11" stroke="var(--leaf-green)" stroke-width="1"/></svg>
      www.bramblefordyards.example
    </li>
  </ul>

  <div class="person">
    <p class="person__name">Dorian Pell</p>
    <p class="person__role">Director</p>
  </div>
  <div class="rule rule--name"></div>
</section>

</body>
</html>
```